New Business Card Design Project

Use the flyer uploaded and website www.brightoakbuilders.com for inspiration.
List Our Services on Backside of business cards
Marcus Delling
Harborline Builders Inc.
Licensed General Contractors
858-471-6093

Contact Information for Business Card

Use the flyer uploaded and website www.brightoakbuilders.com for inspiration. List Our Services on Backside of business cards Marcus Delling Harborline Builders Inc. Licensed General Contractors 858-471-6093

```html
<!DOCTYPE html>
<html lang="en">
<head>
<meta charset="utf-8">
<title>Harborline Builders – Business Card</title>
<link href="https://fonts.googleapis.com/css2?family=Cinzel:wght@400&family=Roboto:wght@400&display=swap" rel="stylesheet">
<style>
  :root {
    --stage: #2b2b2c;
    --card: #121213;
    --card-edge: #1f1f21;
    --ink: #f2f2f2;
    --ink-soft: #cfcfd2;
    --bullet: #3d8fe0;
  }
  * { box-sizing: border-box; margin: 0; padding: 0; }
  html, body { width: 1200px; height: 689px; overflow: hidden; background: var(--stage); }
  .canvas {
    width: 1200px; height: 689px;
    display: flex; align-items: center; justify-content: center; gap: 48px;
  }
  .card {
    position: relative;
    width: 540px; height: 309px;
    background: var(--card);
    border-radius: 18px;
    border: 1px solid var(--card-edge);
    box-shadow: 0 14px 30px rgba(0,0,0,.45);
    overflow: hidden;
    color: var(--ink);
  }
  /* Back: services */
  .services {
    position: absolute; left: 44px; top: 62px;
    list-style: none;
    font-family: "Roboto", sans-serif; font-size: 17px; line-height: 21px;
  }
  .services li { display: flex; align-items: center; gap: 10px; }
  .services li::before {
    content: ""; width: 6px; height: 6px; border-radius: 50%;
    background: var(--bullet); flex: none;
  }
  /* Front */
  .brand {
    position: absolute; left: 40px; top: 52px;
    font-family: "Cinzel", serif; font-size: 22px; letter-spacing: 2px;
    color: var(--ink);
  }
  .person {
    position: absolute; left: 40px; top: 140px;
    font-family: "Cinzel", serif; font-size: 24px; letter-spacing: 1.5px;
  }
  .contact {
    position: absolute; left: 40px; top: 190px;
    list-style: none;
    font-family: "Roboto", sans-serif; font-size: 16px; line-height: 24px;
  }
  .contact li { display: flex; align-items: center; gap: 10px; }
  .contact svg { width: 15px; height: 15px; flex: none; }
  .company {
    position: absolute; right: 34px; top: 120px; text-align: right;
    font-family: "Roboto", sans-serif; font-size: 16px; line-height: 22px;
    color: var(--ink-soft);
  }
  .divider {
    position: absolute; left: 300px; top: 110px; width: 1px; height: 160px;
    background: #2a2a2d;
  }
</style>
</head>
<body>
<main class="canvas">
  <section class="card card-back" aria-label="Card back – services">
    <ul class="services">
      <li>Remodel: Kitchen &amp; Bath</li>
      <li>Painting: Interior &amp; Exterior</li>
      <li>Flooring: Carpet, Vinyl, Wood</li>
      <li>Window &amp; Door Replacement</li>
      <li>Plumbing: Repairs &amp; Upgrades</li>
      <li>Energy-Efficient Upgrades</li>
      <li>Deck &amp; Patio Construction</li>
      <li>Water &amp; Mold Damage</li>
      <li>Garage Renovation</li>
    </ul>
  </section>

  <section class="card card-front" aria-label="Card front – contact">
    <div class="brand">Harborline Builders</div>
    <div class="person">MARCUS DELLING</div>
    <ul class="contact">
      <li>
        <svg viewBox="0 0 16 16" fill="none" stroke="currentColor" stroke-width="1.6"><path d="M4 1.5l2.5 3-1.5 2a8 8 0 0 0 4.5 4.5l2-1.5 3 2.5-1.5 2.5C7 14.5 1.5 9 1.5 3z"/></svg>
        858-471-6093
      </li>
      <li>
        <svg viewBox="0 0 16 16" fill="none" stroke="currentColor" stroke-width="1.6"><rect x="1.5" y="3.5" width="13" height="9"/><path d="M1.5 3.5l6.5 5 6.5-5"/></svg>
        info@brightoakbuilders.com
      </li>
      <li>
        <svg viewBox="0 0 16 16" fill="none" stroke="currentColor" stroke-width="1.4"><circle cx="8" cy="8" r="6.5"/><ellipse cx="8" cy="8" rx="3" ry="6.5"/><path d="M1.5 8h13M2.5 5h11M2.5 11h11"/></svg>
        BrightOakBuilders.com
      </li>
    </ul>
    <div class="divider"></div>
    <div class="company">
      <p>Harborline Builders Inc.</p>
      <p>Licensed General Contractors</p>
    </div>
  </section>
</main>
</body>
</html>
```